Redesign and move to Wordpress for corvandel.com

Our website needs a redesign and at the same time we are moving it to Wordpress. Please help us with a new digital professional look and feel.

We are an Australian Software Engineering company specialising in advanced software development using in A.I., PLatform Engineering, Integration and Cloud. See the current corvandel.com for more information about us.

```html
<!DOCTYPE html>
<html lang="en">
<head>
<meta charset="utf-8">
<title>Corvandel — Tomorrow Delivered Today</title>
<link href="https://fonts.googleapis.com/css2?family=Josefin+Sans:wght@400;600;700&family=Jost:wght@400;500;600&display=swap" rel="stylesheet">
<style>
:root{
  --navy:#0b1a33;
  --blue:#1b5aa8;
  --blue-dark:#154a8e;
  --teal:#3ebfb8;
  --teal-light:#5fd0c9;
  --ink:#1d2230;
  --muted:#6b7280;
  --line:#e6e9ef;
  --white:#ffffff;
}
*{box-sizing:border-box;margin:0;padding:0}
html,body{width:1200px;height:4216px;overflow:hidden}
body{position:relative;font-family:'Jost',sans-serif;color:var(--ink);background:var(--white)}
.abs{position:absolute}
.head{font-family:'Josefin Sans',sans-serif;font-weight:700;text-transform:uppercase}
.photo{position:absolute}
.btn{position:absolute;display:flex;align-items:center;justify-content:center;font-weight:500;font-size:16px}

/* hero */
.hero{left:0;top:0;width:1200px;height:605px;background:radial-gradient(circle at 75% 40%,#1d5b86 0%,#0d2a47 35%,#050b18 75%)}
.brand-box{left:0;top:0;width:350px;height:95px;background:var(--teal);display:flex;align-items:center;padding-left:46px;gap:14px}
.brand-box .mark{width:28px;height:28px;border:3px solid #fff}
.brand-box span{color:#fff;font-size:36px;letter-spacing:1px}
.nav{top:40px;left:497px;display:flex;gap:0;color:#fff;font-size:16px}
.nav a{position:absolute;white-space:nowrap;color:#fff;text-decoration:none}
.nav a.active{color:var(--teal-light);text-decoration:underline}
.hero-title{left:110px;top:212px;color:#fff;font-size:62px;line-height:76px}
.hero-sub{left:110px;top:368px;color:#fff;font-size:18px;line-height:31px}
.hero-bar{left:56px;top:310px;width:2px;height:95px;background:#fff}
.hero-notch{left:560px;top:578px;width:80px;height:40px;background:#fff;border-radius:40px 40px 0 0}

/* who */
.who-title{left:657px;top:716px;font-size:32px;color:var(--navy)}
.rule{position:absolute;height:3px;background:var(--blue)}
.dot{position:absolute;width:12px;height:12px;background:var(--blue)}
.who-text{left:657px;top:795px;width:430px;font-size:15px;line-height:32px;color:var(--muted)}
.who-blue{left:657px;top:996px;width:430px;font-size:16px;line-height:32px;color:var(--blue)}

/* logos */
.logos{left:111px;top:1247px;width:977px;height:148px;background:#fff;box-shadow:0 4px 20px rgba(0,0,0,.08);display:flex;z-index:2}
.logos div{flex:1;display:flex;align-items:center;justify-content:center;gap:10px;border-right:1px solid var(--line);font-size:30px;font-weight:600;color:#333}
.logos div:last-child{border:none}
.logos i{width:26px;height:26px;background:#555;display:inline-block}
.logos-bar{left:111px;top:1395px;width:977px;height:10px;background:var(--teal);z-index:2}

.offer{left:0;top:1325px;width:1200px;height:1113px;background:linear-gradient(180deg,#1b5aa8,#174b8c 60%,#1a5aa5)}
.card{position:absolute;background:#fff}
.card .cap{position:absolute;font-size:13px}
.card h4{font-family:'Jost',sans-serif;font-weight:600;font-size:13px;color:#222;text-transform:uppercase}
.card p{font-size:12px;color:var(--muted)}
.icon{position:absolute;width:50px;height:50px;border-radius:50%;background:#fff;border:2px solid #e4eef8;display:flex;align-items:center;justify-content:center}
.icon b{width:22px;height:22px;border-radius:50%;background:var(--blue)}
.mini{position:absolute;width:112px;height:38px;background:var(--blue);color:#fff;font-size:12px;font-weight:600;display:flex;align-items:center;justify-content:center}

/* booking */
.cal{left:111px;top:2557px;width:489px;height:610px;background:var(--blue)}
.cal .d{position:absolute;width:54px;text-align:center;font-size:13px;color:rgba(255,255,255,.45)}
.cal .d.on{color:#fff;font-weight:600}
.cal .h{position:absolute;width:54px;text-align:center;font-size:13px;font-weight:600;color:#fff}
.book{left:600px;top:2557px;width:488px;height:533px;background:#fff;box-shadow:0 4px 24px rgba(0,0,0,.08)}

/* news */
.news{position:absolute;background:#fff;box-shadow:0 2px 16px rgba(0,0,0,.08);width:308px;height:437px;text-align:center}
.tag{position:absolute;left:40px;top:214px;width:228px;height:36px;background:var(--teal);color:#fff;font-size:11px;font-weight:600;display:flex;align-items:center;justify-content:center}
.news h5{position:absolute;left:22px;width:264px;top:282px;font-size:12.5px;font-weight:600;line-height:22px;text-transform:uppercase}
.news p{position:absolute;left:28px;width:252px;top:336px;font-size:11.5px;line-height:22px;color:var(--muted)}

.social{position:absolute;width:40px;height:40px;border-radius:50%;background:var(--teal);display:flex;align-items:center;justify-content:center}
.social b{width:12px;height:12px;background:#fff;border-radius:2px}
</style>
</head>
<body>

<!-- HERO -->
<section class="abs hero">
  <div class="photo" role="img" aria-label="Hand touching a glowing digital technology interface" style="left:560px;top:60px;width:640px;height:540px;background:radial-gradient(circle at 55% 45%,rgba(80,170,220,.45),rgba(5,12,25,0) 65%)"></div>
</section>
<div class="abs brand-box"><div class="mark"></div><span>corvandel</span></div>
<nav class="abs nav">
  <a class="active" style="left:0">Home</a>
  <a style="left:110px">About Us</a>
  <a style="left:245px">Our Services</a>
  <a style="left:403px">Blogs</a>
  <a style="left:508px">Contact Us</a>
</nav>
<div class="abs hero-bar"></div>
<h1 class="abs head hero-title">Tomorrow<br>Delivered Today</h1>
<p class="abs hero-sub">We are a software engineering company focused on<br>Kestrix Integration &amp; Custom Application Development.</p>
<a class="btn" style="left:110px;top:452px;width:131px;height:40px;background:var(--blue);color:#fff">Get Started</a>
<div class="abs hero-notch"></div>
<svg class="abs" style="left:591px;top:590px" width="18" height="24" viewBox="0 0 18 24"><rect x="1" y="1" width="16" height="22" rx="8" fill="#b8bcc4"/><path d="M9 6v9M5 12l4 4 4-4" stroke="#fff" stroke-width="2" fill="none"/></svg>

<!-- WHO WE ARE -->
<div class="photo" role="img" aria-label="Monitor showing code on a desk at night" style="left:111px;top:691px;width:228px;height:190px;background:linear-gradient(135deg,#2a1a12,#a0541e 55%,#1d2a3a)"></div>
<div class="photo" role="img" aria-label="Two developers working at computers in an office" style="left:358px;top:691px;width:227px;height:252px;background:linear-gradient(160deg,#6b6158,#2e3136 60%,#1a1c20)"></div>
<div class="photo" role="img" aria-label="Hands typing on a keyboard with colourful light streams" style="left:111px;top:900px;width:228px;height:252px;background:linear-gradient(135deg,#1c1a4a,#7a3a8f 45%,#d06a3a 70%,#1a1f4a)"></div>
<div class="photo" role="img" aria-label="Developer thinking at a laptop" style="left:358px;top:962px;width:227px;height:190px;background:linear-gradient(150deg,#b9b3aa,#6a553f 55%,#2a2a2e)"></div>
<h2 class="abs head who-title">Who We Are</h2>
<div class="rule" style="left:657px;top:770px;width:94px"></div><div class="dot" style="left:740px;top:766px"></div>
<p class="abs who-text">At Corvandel, we craft bespoke software solutions that are not available on the market. By building organizations market-leading products, process automation, legacy system enablement, or advanced intelligent systems, we empower our customers to achieve a competitive edge in their industry.</p>
<p class="abs who-blue">We have been on a mission to make complex custom enterprise integration accessible to any organization.</p>
<a class="btn" style="left:657px;top:1081px;width:130px;height:41px;background:var(--blue);color:#fff">Read More</a>

<!-- WHAT WE OFFER -->
<section class="abs offer"></section>
<div class="abs logos">
  <div>Norvale</div>
  <div><i></i>Kestrix</div>
  <div>Tarrow</div>
  <div>Brightfund</div>
</div>
<div class="abs logos-bar"></div>

<h2 class="abs head" style="left:0;width:1200px;top:1475px;text-align:center;color:#fff;font-size:32px">What We Offer</h2>
<div class="abs" style="left:528px;top:1531px;width:146px;height:2px;background:#fff"></div>
<div class="abs" style="left:595px;top:1526px;width:12px;height:12px;background:#fff"></div>

<div class="card" style="left:99px;top:1575px;width:492px;height:347px">
  <div class="photo" role="img" aria-label="Person using a smartphone with logistics icons" style="left:0;top:0;width:492px;height:272px;background:linear-gradient(120deg,#2a4d6e,#4f90c0 45%,#e0a050 80%)"></div>
  <div class="icon" style="left:24px;top:285px"><b></b></div>
  <div class="cap" style="left:88px;top:290px"><h4>Enterprise Systems Integration</h4><p>Automate your business processes</p></div>
  <div class="mini" style="left:354px;top:292px">View Details</div>
</div>
<div class="card" style="left:610px;top:1575px;width:491px;height:347px">
  <div class="photo" role="img" aria-label="Engineer with tablet in front of data screens" style="left:0;top:0;width:491px;height:272px;background:linear-gradient(120deg,#0d2644,#2b6aa0 50%,#0a1c33)"></div>
  <div class="icon" style="left:24px;top:285px"><b></b></div>
  <div class="cap" style="left:88px;top:290px"><h4>Platform Engineering</h4><p>For organisations looking to manage..</p></div>
  <div class="mini" style="left:354px;top:292px">View Details</div>
</div>
<div class="card" style="left:99px;top:1945px;width:325px;height:355px">
  <div class="photo" role="img" aria-label="Connected glowing cubes network" style="left:0;top:0;width:325px;height:273px;background:linear-gradient(150deg,#0b1d33,#1f5a8c 55%,#0b1626)"></div>
  <div class="icon" style="left:137px;top:248px"><b></b></div>
  <div class="cap" style="left:0;width:325px;top:307px;text-align:center"><h4>Microservices</h4><p>Leverage Microservices Architecture</p></div>
</div>
<div class="card" style="left:439px;top:1945px;width:323px;height:355px;border:6px solid #fff">
  <div class="photo" role="img" aria-label="Glowing cloud above a circuit board" style="left:0;top:0;width:311px;height:267px;background:linear-gradient(160deg,#123a6e,#2f7fd0 50%,#e29a3a 90%)"></div>
  <div class="icon" style="left:130px;top:242px;background:var(--blue)"><b style="background:#fff"></b></div>
  <div class="cap" style="left:0;width:311px;top:301px;text-align:center"><h4>iPaaS</h4><p>Integration Platform as a Service</p></div>
</div>
<div class="card" style="left:776px;top:1945px;width:325px;height:355px">
  <div class="photo" role="img" aria-label="Robot hand reaching toward a glowing light" style="left:0;top:0;width:325px;height:273px;background:radial-gradient(circle at 60% 50%,#ffb070,#1e4a7a 35%,#0a1830 80%)"></div>
  <div class="icon" style="left:137px;top:248px"><b></b></div>
  <div class="cap" style="left:0;width:325px;top:307px;text-align:center"><h4>Assistant / AI Agents</h4><p>The future of business AI</p></div>
</div>
<a class="btn" style="left:455px;top:2330px;width:129px;height:40px;background:var(--teal);color:#fff">View More</a>
<a class="btn" style="left:609px;top:2330px;width:137px;height:40px;background:#fff;color:var(--teal)">Join With Us</a>

<!-- BOOKING -->
<section class="abs cal">
  <div class="photo" role="img" aria-label="Portrait of the CTO" style="left:36px;top:38px;width:86px;height:86px;border-radius:50%;background:radial-gradient(circle,#9a7a62,#3c2e26)"></div>
  <div class="abs head" style="left:152px;top:54px;color:#fff;font-size:22px">Meet With Our CTO</div>
  <div class="abs" style="left:152px;top:88px;color:var(--teal-light);font-size:18px">January 2025 &nbsp;⇕</div>
  <div class="h" style="left:31px;top:168px">SUN</div><div class="h" style="left:95px;top:168px">MON</div><div class="h" style="left:158px;top:168px">TUE</div><div class="h" style="left:222px;top:168px">WED</div><div class="h" style="left:286px;top:168px">THU</div><div class="h" style="left:349px;top:168px">FRI</div><div class="h" style="left:413px;top:168px">SAT</div>
  <div class="d" style="left:222px;top:225px">1</div><div class="d" style="left:286px;top:225px">2</div><div class="d" style="left:349px;top:225px">3</div><div class="d" style="left:413px;top:225px">4</div>
  <div class="d" style="left:31px;top:282px">5</div><div class="d" style="left:95px;top:282px">6</div><div class="d" style="left:158px;top:282px">7</div><div class="d" style="left:222px;top:282px">8</div><div class="d" style="left:286px;top:282px">9</div><div class="d" style="left:349px;top:282px">10</div><div class="d" style="left:413px;top:282px">11</div>
  <div class="d" style="left:31px;top:338px">12</div><div class="d" style="left:95px;top:338px">13</div><div class="d" style="left:158px;top:338px">14</div>
  <div class="abs" style="left:223px;top:315px;width:52px;height:52px;border-radius:50%;background:#fff"></div>
  <div class="d on" style="left:222px;top:338px;color:var(--blue)">15</div><div class="d on" style="left:286px;top:338px">16</div><div class="d on" style="left:349px;top:338px">17</div><div class="d" style="left:413px;top:338px">18</div>
  <div class="d" style="left:31px;top:395px">19</div><div class="d" style="left:95px;top:395px">20</div><div class="d" style="left:158px;top:395px">21</div><div class="d on" style="left:222px;top:395px">22</div><div class="d on" style="left:286px;top:395px">23</div><div class="d on" style="left:349px;top:395px">24</div><div class="d" style="left:413px;top:395px">25</div>
  <div class="d" style="left:31px;top:451px">26</div><div class="d" style="left:95px;top:451px">27</div><div class="d" style="left:158px;top:451px">28</div><div class="d on" style="left:222px;top:451px">29</div><div class="d on" style="left:286px;top:451px">30</div><div class="d on" style="left:349px;top:451px">31</div>
  <a class="btn" style="left:60px;top:517px;width:369px;height:55px;background:var(--teal);color:#fff;font-size:18px">Book An Obligation</a>
</section>
<section class="abs book">
  <div class="abs" style="left:56px;top:50px;display:flex;align-items:center;gap:14px"><div style="width:40px;height:40px;border:4px solid var(--teal-light)"></div><span style="font-size:46px;color:var(--teal-light);letter-spacing:1px">corvandel</span></div>
  <h3 class="abs head" style="left:54px;top:137px;font-size:32px;color:var(--ink)">Book An Obligation</h3>
  <p class="abs" style="left:54px;top:184px;font-size:17px;color:#444">Free consultation with our Lead Technologist</p>
  <div class="rule" style="left:54px;top:224px;width:95px"></div><div class="dot" style="left:137px;top:219px"></div>
  <div class="abs" style="left:56px;top:272px;font-size:17px;color:#444;font-weight:500">MEETING DURATION</div>
  <div class="abs" style="left:256px;top:256px;width:107px;height:42px;background:var(--teal);color:#fff;font-size:17px;display:flex;align-items:center;justify-content:center">30 Mins</div>
  <div class="abs" style="left:56px;top:328px;font-size:18px;color:var(--blue);font-weight:500">What time works best?</div>
  <div class="abs" style="left:56px;top:363px;font-size:17px;color:#555">Showing times for January 15, 2025</div>
  <div class="abs" style="left:56px;top:408px;font-size:18px;color:var(--teal)">UTC +05:30 New Delhi, Mumbai, Calcutta</div>
  <div class="abs" style="left:57px;top:442px;width:386px;height:50px;background:#f2f4f8;border:1px solid var(--line);font-size:14px;color:#666;display:flex;align-items:center;justify-content:space-between;padding:0 24px"><span>Choose Time</span><span>⇕</span></div>
</section>
<div class="abs" style="left:816px;top:3130px;font-size:17px;color:#444">Follow Us On:</div>
<div class="social" style="left:952px;top:3121px"><b></b></div>
<div class="social" style="left:1000px;top:3121px"><b></b></div>
<div class="social" style="left:1048px;top:3121px"><b></b></div>

<!-- NEWS -->
<h2 class="abs head" style="left:0;width:1200px;top:3236px;text-align:center;font-size:32px;color:var(--ink)">Latest News &amp; Articles</h2>
<div class="abs" style="left:528px;top:3294px;width:146px;height:2px;background:var(--blue)"></div>
<div class="dot" style="left:595px;top:3289px"></div>

<article class="news" style="left:115px;top:3335px">
  <div class="photo" role="img" aria-label="Friendly robot beside a laptop with holographic panels" style="left:0;top:0;width:308px;height:240px;background:linear-gradient(150deg,#0e2b4e,#2d6ea8 55%,#0b1a30)"></div>
  <div class="tag">AI IN SOFTWARE ENGINEERING</div>
  <h5>10 Unexpected Ways to Use CodeMate Assistant</h5>
  <p>CodeMate is widely known for its code generation feature. Learn how the AI assistant's abilities can extend beyond just code generation.</p>
</article>
<article class="news" style="left:446px;top:3335px;border:3px solid var(--teal)">
  <div class="photo" role="img" aria-label="Worker in hard hat with augmented reality display" style="left:0;top:0;width:302px;height:237px;background:linear-gradient(150deg,#1a3a55,#d08a30 55%,#2a2018)"></div>
  <div class="tag" style="left:37px;top:211px;background:var(--blue-dark)">INDUSTRY RESEARCH</div>
  <h5 style="left:19px;top:279px">A General-Purpose Framework for Prompt Optimization</h5>
  <p style="left:25px;top:333px">Large language models (LLMs) have revolutionized various tasks, but prompt engineering remains a challenge. Enter PROMPTA: an open-source tool</p>
</article>
<article class="news" style="left:779px;top:3335px">
  <div class="photo" role="img" aria-label="Business people silhouetted against a connected city skyline" style="left:0;top:0;width:308px;height:240px;background:linear-gradient(180deg,#6d7f95,#b59a78 55%,#2b2d33)"></div>
  <div class="tag">CORESTACK &amp; SKYVAULT</div>
  <h5>Lumora's New Flagship Multimodal Model Now in Preview on Skyvault.</h5>
  <p>This groundbreaking multimodal model integrates text, vision, and audio capabilities, setting a new standard for generative and conversational AI experiences.</p>
</article>
<div class="abs" style="left:1120px;top:3523px;width:45px;height:45px;background:#e9f6f5;display:flex;align-items:center;justify-content:center"><svg width="14" height="10"><path d="M1 8l6-6 6 6" stroke="var(--teal)" stroke-width="2" fill="none"/></svg></div>
<div class="abs" style="left:1120px;top:3580px;width:45px;height:45px;background:var(--teal);display:flex;align-items:center;justify-content:center"><svg width="14" height="10"><path d="M1 2l6 6 6-6" stroke="#fff" stroke-width="2" fill="none"/></svg></div>

<!-- NEWSLETTER -->
<section class="abs" style="left:0;top:3813px;width:1200px;height:327px;background:linear-gradient(180deg,#35b5ae,#2fa9a2)"></section>
<h2 class="abs head" style="left:0;width:1200px;top:3905px;text-align:center;color:#fff;font-size:30px">Register To Our Newsletter To Find Out More.</h2>
<div class="abs" style="left:528px;top:3970px;width:146px;height:2px;background:#fff"></div>
<div class="abs" style="left:595px;top:3965px;width:12px;height:12px;background:#fff"></div>
<p class="abs" style="left:0;width:1200px;top:3997px;text-align:center;color:#fff;font-size:18px">Australia's Largest health charity implements Corvandel API Msg Bus</p>
<div class="abs" style="left:275px;top:4038px;width:412px;height:43px;background:#fff;font-size:13px;color:#666;display:flex;align-items:center;padding-left:28px">Email Address</div>
<a class="btn" style="left:710px;top:4038px;width:215px;height:43px;background:var(--blue);color:#fff;font-size:15px;font-weight:600">Subscribe Here</a>

<!-- FOOTER -->
<footer class="abs" style="left:0;top:4140px;width:1200px;height:76px;background:var(--blue)"></footer>
<div class="abs" style="left:111px;top:4167px;color:#fff;font-size:16px">(C) Copyright | All Rights Reserved</div>
<div class="social" style="left:952px;top:4158px"><b></b></div>
<div class="social" style="left:1000px;top:4158px"><b></b></div>
<div class="social" style="left:1048px;top:4158px"><b></b></div>

</body>
</html>
```